Business card for my new company (Accounting firm)

I need a business card for my new business Brightwell Advisory and Ledger SA. Our services are accounting, tax, audit and financial management. Our customers are small companies, start-ups and new companies. The final design has to show financial security, trust and growth. Please find our logo attached to the business card. Text for the business card: Brightwell Advisory and Ledger SA Tomas Varenholt Director and Founder Certified Accountant Tel. 022 418 57 34 tv@clairevalconseil.ch www.clairevalconseil.ch Rue des Vergières 27 1201 Geneva
Target Market(s)
Our customers are small companies, start-ups and new companies.
Industry/Entity Type
Finance And Accounting
Contact Information for Business Card
Claireval Conseil et Comptes SA
Tomas Varenholt
Directeur et Fondateur
Expert-comptable diplômé
Tél. 022 418 57 34
tv@clairevalconseil.ch
www.clairevalconseil.ch
Rue des Vergières 27
1201 Genève

```html
<!DOCTYPE html>
<html lang="fr">
<head>
<meta charset="utf-8">
<title>Claireval Conseil et Comptes SA – Carte de visite</title>
<link href="https://fonts.googleapis.com/css2?family=Roboto:wght@400;500;700&display=swap" rel="stylesheet">
<style>
  :root {
    --backdrop: #3a3a3c;
    --card: #1e1f22;
    --accent: #2a9fdc;
    --accent-deep: #1f78b8;
    --ink-light: #f2f4f6;
    --ink-muted: #d6d9dd;
    --emboss: #3b3d42;
  }
  * { margin: 0; padding: 0; box-sizing: border-box; }
  html, body {
    width: 799px; height: 1200px; overflow: hidden;
    background: var(--backdrop);
    font-family: "Roboto", Arial, sans-serif;
  }
  .sheet {
    position: relative; width: 799px; height: 1200px;
    display: flex; flex-direction: column; align-items: center; justify-content: space-around;
    padding: 60px 0;
  }
  .card {
    position: relative; width: 620px; height: 354px;
    background: var(--card);
    box-shadow: 0 14px 30px rgba(0,0,0,.45);
    overflow: hidden;
  }

  /* Front */
  .card-front .accent-band {
    position: absolute; left: 0; right: 0; bottom: 0; height: 14px;
    background: var(--accent);
  }
  .card-front .brand {
    position: absolute; left: 0; right: 0; top: 140px;
    display: flex; align-items: center; justify-content: center; gap: 14px;
  }
  .card-front .brand-mark { width: 30px; height: 30px; background: var(--emboss); }
  .card-front .brand-name {
    font-weight: 700; font-size: 52px; letter-spacing: 2px; color: var(--emboss);
  }

  /* Back */
  .card-back .holder { position: absolute; left: 40px; top: 36px; }
  .holder-name { font-weight: 700; font-size: 24px; color: var(--accent); margin-bottom: 6px; }
  .holder-role { font-size: 14px; line-height: 1.35; color: var(--ink-muted); }

  .card-back .contact { position: absolute; left: 40px; top: 160px; color: var(--ink-light); font-size: 16px; }
  .address { line-height: 1.35; margin-bottom: 8px; padding-left: 26px; }
  .contact-list { list-style: none; }
  .contact-list li { display: flex; align-items: center; gap: 10px; line-height: 1.6; }
  .contact-list svg { width: 15px; height: 15px; fill: var(--accent-deep); flex: none; }

  .card-back .brand {
    position: absolute; right: 34px; bottom: 34px;
    display: flex; align-items: center; gap: 12px;
  }
  .card-back .brand-mark { width: 26px; height: 26px; background: var(--accent); }
  .card-back .brand-name { font-weight: 700; font-size: 40px; letter-spacing: 1.5px; color: var(--ink-light); }
</style>
</head>
<body>
<main class="sheet">

  <section class="card card-front" aria-label="Recto">
    <div class="brand">
      <span class="brand-mark"></span>
      <span class="brand-name">CLAIREVAL</span>
    </div>
    <div class="accent-band"></div>
  </section>

  <section class="card card-back" aria-label="Verso">
    <div class="holder">
      <p class="holder-name">Tomas Varenholt</p>
      <p class="holder-role">Directeur et Fondateur<br>Expert-comptable diplômé</p>
    </div>

    <div class="contact">
      <p class="address">Rue des Vergières 27<br>1201 Genève</p>
      <ul class="contact-list">
        <li>
          <svg viewBox="0 0 24 24" aria-hidden="true"><path d="M6.6 10.8a15.1 15.1 0 0 0 6.6 6.6l2.2-2.2a1 1 0 0 1 1-.25 11.4 11.4 0 0 0 3.6.57 1 1 0 0 1 1 1V20a1 1 0 0 1-1 1A17 17 0 0 1 3 4a1 1 0 0 1 1-1h3.5a1 1 0 0 1 1 1c0 1.25.2 2.45.57 3.57a1 1 0 0 1-.25 1z"/></svg>
          <span>022 418 57 34</span>
        </li>
        <li>
          <svg viewBox="0 0 24 24" aria-hidden="true"><path d="M2 5h20v14H2z M3.5 6.5 12 13l8.5-6.5" stroke="#1e1f22" stroke-width="1.5"/></svg>
          <span>tv@clairevalconseil.ch</span>
        </li>
        <li>
          <svg viewBox="0 0 24 24" aria-hidden="true"><circle cx="12" cy="12" r="10"/><path d="M2 12h20M12 2c3 3 3 17 0 20M12 2c-3 3-3 17 0 20" stroke="#1e1f22" stroke-width="1.4" fill="none"/></svg>
          <span>www.clairevalconseil.ch</span>
        </li>
      </ul>
    </div>

    <div class="brand">
      <span class="brand-mark"></span>
      <span class="brand-name">CLAIREVAL</span>
    </div>
  </section>

</main>
</body>
</html>
```